Luxury Wine Label for New Startup Winery

We need a wine label for our new winery startup. We have worked with a local designer but do not feel the resulting label / logo have the elevation required to present our brand as a luxury wine. Our winery is called "Quailbrook Vineyards" and we are focused on extremely high quality hand crafted artisan and estate wines from the Pacific Northwest.
We would like to see designs that utilize a tree line, or other imagery that represents the "Quailbrook" part of our company name. Another interesting feature could be wood grain.
A logo will be required based on your design so please design with this in mind:
This logo should be consistent with the wine bottle label design, and should be representative of our high end exclusive wine while giving a sense of place (Oregon/ Pacific Northwest.)
I will supply an image of the design we received from our local designer, PLEASE NOTE: in general we do like wood grain and tree line concepts but feel the execution was poorly done.
ATTN: Logo design should be suitable for use on: Bottles (Red wine/rose/white wine), Bussiness cards, vehicle signage, business signage, etc
P.S.:
If you have a design that is not outside the box we are still interested in seeing it.
Label is for a burgundy style bottle with a label height of 3.5 - 4" and a width of 3.5-4"
any label <= 4"x4" and >=3.5"x3.5" will be acceptable:
HOWEVER Width should be greater than or equal to height due to the bottle format
Target Market(s)
Wine enthusiasts with adequate discretionary budgets to afford $100 bottles of wine.
Industry/Entity Type
Wine / Winery
Requirements
Must have
- A sense of luxury, a feel of exclusivity, and a theme consistent with our product and brand name
Nice to have
- Tree line, wood grain or other wood themes. Serif fonts
Should not have
- anything cheesy, off topic, hard to read script fonts or anything that makes the label hard to read from a few feet away or too busy

```html
<!DOCTYPE html>
<html lang="en">
<head>
<meta charset="utf-8">
<title>Quailbrook Vineyards – Syrah Label</title>
<link href="https://fonts.googleapis.com/css2?family=Cinzel:wght@400;500;600&display=swap" rel="stylesheet">
<style>
  :root {
    --backdrop: #f4f3f1;
    --label-black: #121110;
    --gold: #c9a05a;
    --gold-light: #e6c98c;
    --gold-deep: #8f6a2e;
    --wood-dark: #2a1a12;
    --wood-mid: #4a2f1f;
    --wood-light: #5e3d28;
  }
  * { box-sizing: border-box; margin: 0; padding: 0; }
  html, body {
    width: 1200px;
    height: 1200px;
    overflow: hidden;
    background: var(--backdrop);
  }
  .canvas {
    position: relative;
    width: 1200px;
    height: 1200px;
    display: flex;
    align-items: center;
    justify-content: center;
  }
  .wine-label {
    position: relative;
    width: 1040px;
    height: 1000px;
    background: var(--label-black);
    font-family: "Cinzel", "Times New Roman", serif;
    color: var(--gold);
    overflow: hidden;
  }
  .rule-stack {
    position: absolute;
    left: 0;
    width: 100%;
    display: flex;
    flex-direction: column;
    gap: 7px;
  }
  .rule-stack span {
    display: block;
    height: 1px;
    background: var(--gold-deep);
    opacity: 0.7;
  }
  .rule-stack--top { top: 28px; }
  .rule-stack--mid { top: 640px; }

  .brand-mark {
    position: absolute;
    top: 120px;
    left: 0;
    width: 100%;
    display: flex;
    align-items: center;
    justify-content: center;
    gap: 18px;
  }
  .brand-mark__dot {
    width: 22px;
    height: 22px;
    border-radius: 50%;
    background: var(--gold);
  }
  .brand-mark__name {
    font-size: 34px;
    font-weight: 500;
    letter-spacing: 4px;
    color: var(--gold);
  }

  .region {
    position: absolute;
    top: 250px;
    left: 50%;
    transform: translateX(-50%);
    font-size: 36px;
    font-weight: 500;
    letter-spacing: 2px;
    padding: 0 14px 10px;
    border-bottom: 1px solid var(--gold-deep);
    white-space: nowrap;
  }

  .treeline-scene {
    position: absolute;
    top: 330px;
    left: 0;
    width: 100%;
    height: 290px;
    background:
      linear-gradient(170deg, transparent 0%, transparent 30%, rgba(201,160,90,0.55) 55%, rgba(143,106,46,0.35) 70%, transparent 88%),
      linear-gradient(180deg, rgba(230,201,140,0.25) 0%, rgba(201,160,90,0.12) 45%, transparent 100%);
  }

  .wood-band {
    position: absolute;
    top: 690px;
    left: 0;
    width: 100%;
    height: 210px;
    background: linear-gradient(180deg, var(--wood-light) 0%, var(--wood-mid) 40%, var(--wood-dark) 100%);
    display: flex;
    align-items: center;
    justify-content: center;
  }
  .varietal {
    font-size: 118px;
    font-weight: 600;
    letter-spacing: 6px;
    color: var(--gold);
    line-height: 1;
  }

  .vintage-row {
    position: absolute;
    top: 915px;
    left: 0;
    width: 100%;
    display: flex;
    align-items: center;
    gap: 20px;
    padding: 0 20px;
  }
  .vintage-row__rule {
    flex: 1;
    height: 9px;
    border-top: 1px solid var(--gold-deep);
    border-bottom: 1px solid var(--gold-deep);
  }
  .vintage-row__text {
    font-size: 42px;
    font-weight: 500;
    letter-spacing: 2px;
    white-space: nowrap;
  }
  .vintage-row__text .divider { padding: 0 10px; font-weight: 400; }
</style>
</head>
<body>
<main class="canvas">
  <article class="wine-label">
    <div class="rule-stack rule-stack--top"><span></span><span></span><span></span><span></span></div>

    <div class="brand-mark">
      <span class="brand-mark__dot"></span>
      <span class="brand-mark__name">QUAILBROOK VINEYARDS</span>
    </div>

    <p class="region">WILLAMETTE VALLEY</p>

    <div class="treeline-scene" role="img" aria-label="Gold foil evergreen tree line above sweeping rolling hills"></div>

    <div class="rule-stack rule-stack--mid"><span></span><span></span><span></span><span></span><span></span></div>

    <section class="wood-band" role="img" aria-label="Dark walnut wood grain band">
      <h1 class="varietal">SYRAH</h1>
    </section>

    <div class="vintage-row">
      <span class="vintage-row__rule"></span>
      <p class="vintage-row__text">ESTATE<span class="divider">|</span>2023<span class="divider">|</span>GROWN</p>
      <span class="vintage-row__rule"></span>
    </div>
  </article>
</main>
</body>
</html>
```